Consulting firm need a professional powerpoint design

A startup Climate change firm needs a powerpoint template design. The design should reflect aspects of climate change adaptation, resilience and environmental sustainability.

The powerpoint design must convey aspects of nature and climate action for a resilient society.

The last slide of the powerpoint must have a allocation for a slogan such as 'Linking science and decision-making'.

Use the colors in the logo and business card for the powerpoint design.

Target Market(s)

Government and industry

Font styles to use
Sans Serif
Other font styles liked:
• nexa font family

Colors
85cae6
abd037
fece3e

Requirements
Must have
• - Colors used in logo and business card
- Convey science and nature
- Professional
Nice to have
• Many pages
Should not have
• Not complicated

```html
<!DOCTYPE html>
<html lang="en">
<head>
<meta charset="utf-8">
<title>Infographics and Photos — Slide Showcase</title>
<link rel="stylesheet" href="https://fonts.googleapis.com/css2?family=Jost:wght@300&family=Arimo:wght@400;700&display=swap">
<style>
  :root{
    --sky:#85cae6;
    --lime:#abd037;
    --sun:#fece3e;
    --moss:#7d9b3d;
    --pale-sun:#fbe9a9;
    --pale-lime:#dde9b4;
    --navy:#3a4257;
    --ink:#1a1a1a;
    --band:#e3f2f8;
    --hand:#c9cde3;
    --paper:#ffffff;
  }
  *{box-sizing:border-box;margin:0;padding:0}
  html,body{width:1200px;height:240px;overflow:hidden;background:var(--paper)}
  .canvas{position:relative;width:1200px;height:240px;overflow:hidden;font-family:"Arimo",Arial,sans-serif}
  .backdrop{position:absolute;inset:0}
  .section-heading{position:absolute;left:20px;top:16px;font-family:"Jost",sans-serif;font-weight:300;font-size:26px;letter-spacing:19.6px;color:var(--ink);white-space:pre;line-height:1}
  .slide{position:absolute;top:55px;width:268px;height:151px;background:var(--paper);box-shadow:0 3px 6px rgba(0,0,0,.12);border:1px solid #e6eef2;overflow:hidden}
  .page-num{position:absolute;right:19px;bottom:4px;width:12px;height:11px;background:var(--lime);border-radius:4px 4px 0 0;color:#fff;font-size:3.5px;font-weight:700;display:flex;align-items:center;justify-content:center}
  .slide-title{position:absolute;color:var(--navy);font-weight:700;line-height:1.35}
  .bubble{position:absolute;border-radius:50%;display:flex;align-items:center;justify-content:center;text-align:center;font-size:3.7px;font-weight:700;line-height:1.35;color:#fff;padding:4px}
  .bubble.dark-text{color:var(--ink)}
  .petal{position:absolute;width:57px;height:57px;color:#fff;font-size:3.4px;line-height:1.4;padding:28px 6px 0 6px}
  .petal svg{position:absolute;left:22px;top:6px}
  .leaf-tab{position:absolute;width:13px;height:13px;background:var(--lime)}
  .ring{position:absolute;top:39px;width:84px;height:84px;border-radius:50%;border:9px solid var(--lime);background:var(--paper)}
  .ring-text{position:absolute;left:17px;top:33px;font-size:6.6px;font-weight:700;line-height:1.25;color:var(--ink)}
  .ring svg{position:absolute;left:27px;top:5px}
  .rule{position:absolute;top:31px;height:1px}
  .panel{position:absolute;left:134px;top:0;width:134px;height:151px;background:var(--navy)}
  .body-copy{position:absolute;left:12px;top:88px;font-size:7.6px;line-height:1.42;color:var(--ink);width:118px}
</style>
</head>
<body>
<div class="canvas">
  <svg class="backdrop" width="1200" height="240" aria-hidden="true">
    <polygon points="70,241 345,241 1200,28 1200,0 1005,0" fill="var(--band)"/>
  </svg>

  <h1 class="section-heading">INFOGRAPHICS  AND  PHOTOS</h1>

  <!-- Slide 14 -->
  <section class="slide" style="left:15px">
    <div role="img" aria-label="Illustration of an open hand reaching upward" style="position:absolute;left:100px;top:88px;width:92px;height:63px;background:var(--hand);border-radius:60% 40% 0 0;opacity:.85"></div>
    <div class="bubble" style="left:85px;top:5px;width:40px;height:40px;background:var(--sun)">nventore veritatis et quasi architecto beatae vitae dicta sunt explicabo.</div>
    <div class="bubble" style="left:33px;top:32px;width:56px;height:56px;background:var(--sky)">nventore veritatis et quasi architecto beatae vitae dicta sunt explicabo.</div>
    <div class="bubble" style="left:104px;top:44px;width:56px;height:56px;background:var(--lime)">nventore veritatis et quasi architecto beatae vitae dicta sunt explicabo.</div>
    <div class="bubble dark-text" style="left:191px;top:53px;width:40px;height:40px;background:var(--pale-sun)">nventore veritatis et quasi architecto beatae vitae dicta sunt</div>
    <div class="bubble dark-text" style="left:62px;top:90px;width:40px;height:40px;background:var(--pale-lime)">nventore veritatis et quasi architecto beatae vitae dicta sunt.</div>
    <h2 class="slide-title" style="left:150px;top:18px;font-size:11px">Short title<br>here please</h2>
    <span class="page-num">14</span>
  </section>

  <!-- Slide 15 -->
  <section class="slide" style="left:314px">
    <h2 class="slide-title" style="left:12px;top:53px;font-size:11px">Title for this<br>slide here<br>please</h2>
    <span class="leaf-tab" style="left:112px;top:17px;border-radius:0 0 0 9px"></span>
    <span class="leaf-tab" style="left:248px;top:121px;border-radius:0 9px 0 0"></span>
    <div class="petal" style="left:128px;top:17px;background:var(--sun);border-radius:14px 28px 0 4px">
      <svg width="14" height="14" viewBox="0 0 14 14" aria-hidden="true"><circle cx="5" cy="5" r="4" fill="none" stroke="#fff" stroke-width="1.5"/><rect x="3" y="8" width="4" height="5" fill="#fff"/><rect x="8" y="6" width="6" height="6" rx="1" fill="#fff"/></svg>
      nventore veritatis et quasi architecto beatae vitae dicta sunt explicabo.</div>
    <div class="petal" style="left:188px;top:17px;background:var(--sky);border-radius:4px 0 0 0">
      <svg width="14" height="14" viewBox="0 0 14 14" aria-hidden="true"><circle cx="7" cy="5" r="4.5" fill="#fff"/><rect x="6.3" y="8" width="1.4" height="6" fill="#fff"/></svg>
      nventore veritatis et quasi architecto beatae vitae dicta sunt explicabo.</div>
    <div class="petal" style="left:128px;top:77px;background:var(--moss);border-radius:28px 0 0 14px">
      <svg width="14" height="14" viewBox="0 0 14 14" aria-hidden="true"><path d="M3 8a3 3 0 0 1 1-5.5A4 4 0 0 1 11 3a2.6 2.6 0 0 1 0 5z" fill="#fff"/><g fill="#fff"><circle cx="4" cy="10.5" r=".7"/><circle cx="7" cy="10.5" r=".7"/><circle cx="10" cy="10.5" r=".7"/><circle cx="5.5" cy="12.5" r=".7"/><circle cx="8.5" cy="12.5" r=".7"/></g></svg>
      nventore veritatis et quasi architecto beatae vitae dicta sunt explicabo.</div>
    <div class="petal" style="left:188px;top:77px;background:var(--lime);border-radius:0 4px 28px 0">
      <svg width="14" height="14" viewBox="0 0 14 14" aria-hidden="true"><path d="M7 14V6M7 8l-3-3M7 9l3-3" stroke="#fff" stroke-width="1.2"/><circle cx="4" cy="4" r="2" fill="#fff"/><circle cx="10" cy="5" r="2" fill="#fff"/><circle cx="7" cy="3" r="2" fill="#fff"/></svg>
      nventore veritatis et quasi architecto beatae vitae dicta sunt explicabo.</div>
    <span class="page-num">15</span>
  </section>

  <!-- Slide 16 -->
  <section class="slide" style="left:612px">
    <h2 class="slide-title" style="left:12px;top:10px;font-size:8.4px;color:var(--ink)">Please add your title here</h2>
    <span class="rule" style="left:12px;width:82px;background:var(--sun)"></span>
    <span class="rule" style="left:94px;width:81px;background:var(--sky)"></span>
    <span class="rule" style="left:175px;width:81px;background:var(--lime)"></span>
    <div class="ring" style="left:12px">
      <svg width="16" height="16" viewBox="0 0 14 14" aria-hidden="true"><circle cx="5" cy="5" r="4" fill="none" stroke="var(--sky)" stroke-width="1.5"/><rect x="3" y="8" width="4" height="5" fill="var(--sky)"/><rect x="8" y="6" width="6" height="6" rx="1" fill="var(--sky)"/></svg>
      <p class="ring-text">This is just<br>placeholder<br>text only.</p></div>
    <div class="ring" style="left:91px">
      <svg width="16" height="16" viewBox="0 0 14 14" aria-hidden="true"><circle cx="7" cy="5" r="4.5" fill="var(--sky)"/><rect x="6.3" y="8" width="1.4" height="6" fill="var(--sky)"/></svg>
      <p class="ring-text">This is just<br>placeholder<br>text only.</p></div>
    <div class="ring" style="left:171px">
      <svg width="16" height="16" viewBox="0 0 14 14" aria-hidden="true"><path d="M3 8a3 3 0 0 1 1-5.5A4 4 0 0 1 11 3a2.6 2.6 0 0 1 0 5z" fill="var(--sky)"/><g fill="var(--sky)"><circle cx="4" cy="10.5" r=".7"/><circle cx="7" cy="10.5" r=".7"/><circle cx="10" cy="10.5" r=".7"/><circle cx="5.5" cy="12.5" r=".7"/><circle cx="8.5" cy="12.5" r=".7"/></g></svg>
      <p class="ring-text">This is just<br>placeholder<br>text only.</p></div>
    <span class="page-num">16</span>
  </section>

  <!-- Closing slide -->
  <section class="slide" style="left:914px">
    <h2 class="slide-title" style="left:12px;top:30px;font-size:12px;color:#2d3a5a;line-height:1.4">Sed ut perspiciatis<br>unde omnis iste<br>natus</h2>
    <p class="body-copy">Sed ut perspiciatis unde omnis iste natus error sit voluptatem accusantium doloremque laudantium</p>
    <div class="panel">
      <div role="img" aria-label="Illustration of a light bulb sprouting leaves" style="position:absolute;left:12px;top:10px;width:84px;height:134px;background:radial-gradient(ellipse at 50% 40%,rgba(255,255,255,.35),rgba(255,255,255,0) 70%)"></div>
    </div>
  </section>
</div>
</body>
</html>
```